Flyer design for growing electrical business!!!

looking to get some flyers made for advertising to spread the word about my new business to hopefully create more work!
i am letting potential clients know the type of work i do and am trying to sell my services to them.
To be put on double sided A5. the attached document file has what i would like on each page.
i would like my logo on the first page and and colour scheme of black orange and silver for the flyer following the colours of my logo.
On the second page i would like the photo as a focal point on the top half.
The bold writing are my selling points and would like them accentuated.
Industry/Entity Type
Advertising
Look and feel
Each slider illustrates characteristics of the customer's brand and the style your logo design should communicate.

```html
<!DOCTYPE html>
<html lang="en">
<head>
<meta charset="utf-8">
<title>Keystone Volt Electrical – A5 Flyer</title>
<link href="https://fonts.googleapis.com/css2?family=Oswald:wght@500;600;700&family=Roboto+Condensed:wght@400;700&family=Montserrat:wght@800&family=Arimo:wght@400&display=swap" rel="stylesheet">
<style>
  :root{
    --orange:#e85a2a;
    --charcoal:#2b2a29;
    --charcoal-dark:#1f1e1d;
    --silver:#e6e6e6;
    --grey-text:#333;
    --yellow:#ffe600;
    --row-alt:#ececec;
    --white:#fff;
  }
  *{margin:0;padding:0;box-sizing:border-box}
  html,body{width:1200px;height:1200px;overflow:hidden;background:var(--white)}
  .canvas{position:relative;width:1200px;height:1200px}
  .page{position:absolute;top:206px;width:870px;height:1221px;transform:scale(.625);transform-origin:0 0;overflow:hidden;background:var(--white)}
  .page--front{left:35px}
  .page--back{left:616px}
  .page-bg{position:absolute;inset:0}
  .abs{position:absolute;white-space:nowrap}
  .heavy{font-family:"Montserrat",sans-serif;font-weight:800}

  /* front */
  .headline{left:54px;top:40px;font-family:"Oswald",sans-serif;font-weight:700;font-size:78px;line-height:70px;text-transform:uppercase;letter-spacing:-.5px}
  .headline .hl-orange{color:var(--orange)}
  .headline .hl-silver{color:var(--silver)}
  .call-out{left:555px;top:50px;width:380px;transform:rotate(45deg);transform-origin:center;text-align:center;color:var(--charcoal-dark);line-height:1}
  .call-out .co-call{font-size:38px}
  .call-out .co-today{font-size:54px}
  .call-out .co-free-line{font-size:30px}
  .call-out .co-free{color:var(--yellow);font-size:40px}
  .call-out .co-quote{font-size:22px;margin-top:4px}
  .needs-bar{left:0;top:269px;width:556px;height:44px;background:var(--orange)}
  .needs-text{left:54px;top:278px;font-size:23px;color:var(--charcoal-dark)}
  .needs-icon{left:556px;top:271px}
  .services{left:54px;top:346px;font-size:25px;line-height:34px;color:var(--silver)}
  .service-list{list-style:none;font-family:"Roboto Condensed",sans-serif;font-size:31px;color:var(--silver);line-height:48.5px}
  .service-list li{position:relative;padding-left:35px}
  .service-list li::before{content:"";position:absolute;left:0;top:16px;width:24px;height:16px;background:var(--orange);clip-path:polygon(0 50%,40% 0,40% 30%,100% 30%,100% 70%,40% 70%,40% 100%)}
  .service-list .two-line{line-height:38px;padding-top:5px;padding-bottom:5px}
  .service-list .two-line::before{top:12px}
  .list-left{left:52px;top:438px}
  .list-right{left:416px;top:438px}
  .brand-block{left:44px;top:990px;display:flex;align-items:center;gap:14px;font-family:"Oswald",sans-serif;font-weight:600;font-size:40px;line-height:44px;color:var(--orange)}
  .brand-square{width:36px;height:36px;background:var(--orange)}
  .contact{left:361px;top:952px;font-family:"Oswald",sans-serif}
  .contact-name{font-size:32px;font-weight:700;color:var(--charcoal-dark);line-height:46px}
  .contact-phone{font-size:50px;font-weight:700;color:var(--orange);line-height:50px}
  .contact-email{font-family:"Arimo",sans-serif;font-size:26px;color:var(--charcoal-dark);line-height:40px;letter-spacing:.5px}
  .contact-rule{width:322px;height:1px;background:#999;margin:6px 0 12px}
  .contact-reg{font-family:"Roboto Condensed",sans-serif;font-size:25px;color:var(--charcoal-dark);line-height:30px;word-spacing:4px}
  .contact-note{font-family:"Arimo",sans-serif;font-size:18px;line-height:22px;color:var(--grey-text);white-space:normal;width:440px}

  /* back */
  .hero-photo{left:0;top:0;width:870px;height:575px;background:linear-gradient(160deg,#f4f4f2 0%,#e9e6e1 45%,#c9b89e 75%,#8d8a80 100%)}
  .back-brand{left:690px;top:556px;font-family:"Oswald",sans-serif;font-weight:600;font-size:22px;color:var(--silver)}
  .question{left:45px;top:594px;font-size:21px;line-height:29px}
  .question .q-orange{color:var(--orange)}
  .question .q-white{color:var(--white)}
  .divider{left:463px;top:594px;width:2px;height:116px;background:#888}
  .divider-arrow{left:465px;top:614px;width:0;height:0;border-top:12px solid transparent;border-bottom:12px solid transparent;border-left:12px solid #ddd}
  .saving{left:505px;top:586px}
  .saving .s-up{font-size:22px;color:var(--white);line-height:28px}
  .saving .s-amount{font-size:40px;color:var(--orange);line-height:46px}
  .saving .s-bill{font-size:14px;color:var(--white);line-height:20px}
  .saving .s-basis{font-size:13.5px;color:var(--orange);line-height:19px;margin-top:6px}
  .intro{left:45px;top:722px;font-family:"Arimo",sans-serif;font-size:23px;line-height:29px;color:var(--white)}
  .table-title{left:45px;font-family:"Oswald",sans-serif;font-weight:500;font-size:27px;color:var(--white);line-height:34px}
  .tt-prices{top:784px}
  .tt-replace{top:958px}
  .data-table{position:absolute;left:45px;width:776px;border-collapse:collapse;font-family:"Roboto Condensed",sans-serif;font-weight:700;font-size:15px;text-align:center}
  .data-table th{background:var(--orange);color:var(--white);height:24px;border-left:2px solid var(--charcoal);font-weight:700}
  .data-table td{height:24px;color:var(--charcoal-dark);background:var(--white);border-left:2px solid var(--charcoal)}
  .data-table th:first-child,.data-table td:first-child{border-left:none}
  .data-table tr:nth-child(even) td{background:var(--row-alt)}
  .dt-prices{top:824px}
  .dt-replace{top:998px}
  .led-note{left:45px;top:1137px;font-size:17px;color:var(--orange)}
  .led-types{left:45px;top:1160px;display:flex;gap:14px;font-family:"Arimo",sans-serif;font-size:18px;color:var(--white);list-style:none}
  .led-types li{position:relative;padding-left:12px}
  .led-types li::before{content:"";position:absolute;left:0;top:6px;border-top:5px solid transparent;border-bottom:5px solid transparent;border-left:6px solid var(--orange)}
</style>
</head>
<body>
<div class="canvas">

  <section class="page page--front">
    <svg class="page-bg" width="870" height="1221" viewBox="0 0 870 1221">
      <defs>
        <linearGradient id="brushed" x1="0" y1="0" x2="1" y2="0">
          <stop offset="0" stop-color="#2a2928"/>
          <stop offset=".5" stop-color="#383634"/>
          <stop offset="1" stop-color="#262524"/>
        </linearGradient>
      </defs>
      <polygon points="0,0 870,0 870,705 604,901 0,901" fill="url(#brushed)"/>
      <polygon points="454,0 870,0 870,395" fill="var(--orange)"/>
      <polygon points="0,901 604,901 870,705 870,720 610,914 0,914" fill="var(--orange)"/>
    </svg>

    <h1 class="abs headline">
      <span class="hl-orange">Local</span><br>
      <span class="hl-orange">Electrician</span><br>
      <span class="hl-silver">In your area</span>
    </h1>

    <div class="abs call-out heavy">
      <div class="co-call">CALL</div>
      <div class="co-today">TODAY</div>
      <div class="co-free-line">FOR A <span class="co-free">FREE</span></div>
      <div class="co-quote">NO OBLIGATION QUOTE</div>
    </div>

    <div class="abs needs-bar"></div>
    <p class="abs needs-text heavy">FOR ALL YOUR ELECTRICAL NEEDS</p>
    <svg class="abs needs-icon" width="60" height="40" viewBox="0 0 60 40" aria-hidden="true">
      <path d="M0 18 H14 V6 H30 V34 H14 V22 H0 Z M30 10 H48 V15 H30 Z M30 25 H48 V30 H30 Z" fill="var(--orange)"/>
    </svg>

    <p class="abs services heavy">NEW INSTALLATIONS - RENOVATIONS<br>ADDITIONS – UPGRADES – REPAIRS – MAINTENANCE</p>

    <ul class="abs service-list list-left">
      <li>Lighting</li>
      <li>LED lighting</li>
      <li>Garden lighting</li>
      <li>Ceiling fans</li>
      <li>Dimmers</li>
      <li>Smoke detectors</li>
      <li>Power points</li>
      <li>Ovens and Cooktops</li>
      <li>Telephone</li>
    </ul>
    <ul class="abs service-list list-right">
      <li>Data</li>
      <li>TV/Aerial</li>
      <li>Switchboard upgrades</li>
      <li class="two-line">Safety switches (RCDS)<br>and Circuit breakers</li>
      <li>Surge protectors</li>
      <li>Hot Water Units</li>
      <li>Test tagging</li>
    </ul>

    <div class="abs brand-block">
      <span class="brand-square"></span>
      <span>KEYSTONE VOLT<br>ELECTRICAL</span>
    </div>

    <div class="abs contact">
      <p class="contact-name">SAM CARTER</p>
      <p class="contact-phone">0400 123 456</p>
      <p class="contact-email">info@keystonevolt.com.au</p>
      <div class="contact-rule"></div>
      <p class="contact-reg">ABN 12 345 678 901 &nbsp; Lic 100200A</p>
      <p class="contact-note">At Keystone Volt we are fully insured and all work is completed to current Australian Electrical Standards</p>
    </div>
  </section>

  <section class="page page--back">
    <div class="abs hero-photo" role="img" aria-label="Bright modern living room with LED downlights, timber floor, open kitchen and garden view"></div>
    <svg class="page-bg" width="870" height="1221" viewBox="0 0 870 1221">
      <polygon points="0,575 608,575 870,375 870,1221 0,1221" fill="var(--charcoal)"/>
      <polygon points="0,561 600,561 870,358 870,375 608,575 0,575" fill="var(--orange)"/>
      <rect x="0" y="1206" width="870" height="15" fill="var(--orange)"/>
    </svg>

    <p class="abs back-brand">KEYSTONE VOLT</p>

    <p class="abs question heavy">
      <span class="q-orange">ARE YOU SPENDING TOO MUCH<br>ON YOUR ELECTRICITY BILL?</span><br>
      <span class="q-white">ARE YOU SICK AND TIRED OF<br>CHANGING GLOBES?</span>
    </p>
    <div class="abs divider"></div>
    <div class="abs divider-arrow"></div>
    <div class="abs saving heavy">
      <p class="s-up">SAVE UP TO</p>
      <p class="s-amount">$500 OFF</p>
      <p class="s-bill">YOUR ELECTRICITY BILL</p>
      <p class="s-basis">BASED ON CHANGING JUST 22 OF<br>YOUR HALOGEN DOWNLIGHTS TO LED</p>
    </div>

    <p class="abs intro">Why not save yourself some money while adding value to your house!<br>LEDs use at least 75% less electricity and last up to 50 times longer</p>

    <h2 class="abs table-title tt-prices">YEARLY PRICES BASED ON 6 HOURS USE PER DAY @ $0.26 per kWh</h2>
    <table class="data-table dt-prices">
      <tr><th>NUMBER OF DOWNLIGHTS</th><th>HALOGEN GLOBE(50W)</th><th>LED (10W)</th><th>SAVINGS</th></tr>
      <tr><td>1</td><td>$28.47 per year</td><td>$5.69 per year</td><td>$22.78 per year</td></tr>
      <tr><td>10</td><td>$284.70</td><td>$56.90</td><td>$227.80</td></tr>
      <tr><td>20</td><td>$569.40</td><td>$113.80</td><td>$455.60</td></tr>
      <tr><td>30</td><td>$854.10</td><td>$170.70</td><td>$683.40</td></tr>
    </table>

    <h2 class="abs table-title tt-replace">YEARLY REPLACEMENT COSTS BASED ON 6 HOURS USE PER DAY</h2>
    <table class="data-table dt-replace">
      <tr><th>NUMBER OF DOWNLIGHTS</th><th>HALOGEN (AV. 1000 HOURS)</th><th>LED (AV. 50000 HOURS)</th></tr>
      <tr><td>1</td><td>$8</td><td>$0</td></tr>
      <tr><td>10</td><td>$80</td><td>$0</td></tr>
      <tr><td>20</td><td>$160</td><td>$0</td></tr>
      <tr><td>30</td><td>$240</td><td>$0</td></tr>
    </table>

    <p class="abs led-note heavy">Not just downlights, you can change any light to LED</p>
    <ul class="abs led-types">
      <li>Oyster lights</li>
      <li>Directional lights</li>
      <li>Spot lights</li>
      <li>Wall lights</li>
      <li>Pendant lights</li>
      <li>External lights</li>
    </ul>
  </section>

</div>
</body>
</html>
```